Financial Advisor Resource Firm needs business card design

Need business card design for company in Omaha NE called Meridale Circle. We provide resources to financial advisors....workshop programs, retirement analysis, and insurance planning. I would like to see designs that use grays, greens, black, and white colors. The final design should communicate 'collaboration' and be simple yet attractive to financial planning clients. I will attached our logo and another picture of a puzzle piece coming together. I would like the incorporate the puzzle picture somehow, maybe on the back somehow, with color or just the gray scale....OR, the picture be the front of the card with 'Meridale' definition on it (see upload) and then company logo, employee name, title, address on the back (see ppt uploaded). The following disclosure needs to be included somewhere- Advisory services offered through Stonebrook Assets, LLC.
Updates

I uploaded a svg and ai file of the logo

Target Market(s)

Financial planning clients and financial advisors....so pretty diverse age range of about 40-70.

Industry/Entity Type

Financial Planning

Contact Information for Business Card

Tobias L. Fenwright, MBA
Founder/President
5287 E. Larkin Road
Suite 230
Omaha, NE 68190
Phone- (402) 555-0147
Cell- (402) 555-0183
Fax- (402) 555-0129
email- tobias@meridaleplan.example
web address- www.meridaleplan.example

Colors
1b1b1b
474747
d3d3d3
ffffff
9bcb3c
abd036

Requirements
Must have
• Must include logo provided, must be 2 sided, and must have disclosure...all of these items listed in project description

```html
<!DOCTYPE html>
<html lang="en">
<head>
<meta charset="utf-8">
<title>Meridale Circle – Business Card</title>
<link rel="stylesheet" href="https://fonts.googleapis.com/css2?family=Cinzel:wght@600&family=Arimo:wght@400&display=swap">
<style>
  :root {
    --ink: #1b1b1b;
    --charcoal: #474747;
    --silver: #d3d3d3;
    --paper: #ffffff;
    --green: #7fbe3f;
    --green-light: #9bcb3c;
    --backdrop: #ecebe8;
    --serif: "Cinzel", "Times New Roman", serif;
    --sans: "Arimo", Arial, sans-serif;
  }
  * { box-sizing: border-box; margin: 0; padding: 0; }
  html, body {
    width: 1200px; height: 880px; overflow: hidden;
    background: var(--backdrop);
  }
  .canvas { position: relative; width: 1200px; height: 880px; }
  .card {
    position: absolute; width: 620px; height: 354px;
    border-radius: 18px; overflow: hidden;
    box-shadow: 0 10px 28px rgba(0,0,0,.22);
  }
  .card--front { left: 110px; top: 70px; }
  .card--back  { left: 470px; top: 456px; background: var(--paper); }

  .front-photo {
    position: absolute; inset: 0;
    background:
      radial-gradient(ellipse at 70% 40%, #c9c9c9 0%, transparent 55%),
      radial-gradient(ellipse at 30% 75%, #bdbdbd 0%, transparent 50%),
      linear-gradient(135deg, #f4f4f4 0%, #d8d8d8 45%, #b9b9b9 100%);
  }
  .wordmark {
    position: absolute; display: flex; align-items: center; gap: 12px;
    font-family: var(--serif); font-weight: 600; color: var(--ink);
    letter-spacing: .02em; white-space: nowrap;
  }
  .wordmark__dot {
    width: 26px; height: 26px; border-radius: 50%; background: var(--green);
  }
  .card--front .wordmark { left: 150px; top: 150px; font-size: 38px; }
  .card--back  .wordmark { left: 36px; top: 110px; font-size: 36px; }

  .bands { position: absolute; inset: 0; }

  .holder {
    position: absolute; left: 36px; top: 226px; color: var(--paper);
  }
  .holder__name {
    font-family: var(--serif); font-weight: 600; font-size: 17px; letter-spacing: .03em;
  }
  .holder__title { font-family: var(--sans); font-size: 14px; margin-top: 2px; }

  .contact-list {
    position: absolute; list-style: none;
    font-family: var(--sans); font-size: 13.5px; color: var(--paper);
  }
  .contact-list li { display: flex; align-items: center; gap: 9px; height: 21px; white-space: nowrap; }
  .contact-list svg { flex: none; }
  .contact-list--phones { left: 40px; top: 282px; }
  .contact-list--online { left: 336px; top: 238px; }

  .address {
    position: absolute; left: 462px; top: 176px;
    font-family: var(--sans); font-size: 13.5px; line-height: 19px;
    color: var(--paper); font-style: normal; white-space: nowrap;
  }

  .disclosure {
    position: absolute; left: 336px; top: 324px;
    font-family: var(--sans); font-size: 10px; color: var(--silver);
    white-space: nowrap;
  }
</style>
</head>
<body>
<main class="canvas">

  <section class="card card--front" aria-label="Card front">
    <div class="front-photo" role="img" aria-label="Grayscale photo of two hands joining puzzle pieces"></div>
    <div class="wordmark"><span class="wordmark__dot"></span>Meridale Circle</div>
  </section>

  <section class="card card--back" aria-label="Card back">
    <svg class="bands" viewBox="0 0 620 354" width="620" height="354" aria-hidden="true">
      <path d="M0 214 H300 C318 214 318 150 340 150 H620 V354 H0 Z" fill="var(--green)"/>
      <path d="M0 270 H304 C322 270 322 166 344 166 H620 V354 H0 Z" fill="var(--ink)"/>
    </svg>

    <div class="wordmark"><span class="wordmark__dot"></span>Meridale Circle</div>

    <div class="holder">
      <p class="holder__name">TOBIAS L. FENWRIGHT, MBA</p>
      <p class="holder__title">Founder/President</p>
    </div>

    <ul class="contact-list contact-list--phones">
      <li>
        <svg width="15" height="15" viewBox="0 0 16 16"><circle cx="8" cy="8" r="7" fill="none" stroke="var(--green)" stroke-width="1.5"/><path d="M5.5 4.5 L7 6 6.2 7 C6.8 8.3 7.7 9.2 9 9.8 L10 9 11.5 10.5 C10.8 11.6 9.6 11.8 8.5 11.2 6.6 10.2 5.6 9 4.8 7.3 4.3 6.2 4.6 5.1 5.5 4.5 Z" fill="var(--green)"/></svg>
        (402) 555-0147
      </li>
      <li>
        <svg width="15" height="15" viewBox="0 0 16 16"><circle cx="8" cy="8" r="7" fill="none" stroke="var(--green)" stroke-width="1.5"/><rect x="5.6" y="4" width="4.8" height="8" rx="1" fill="none" stroke="var(--green)" stroke-width="1.2"/></svg>
        (402) 555-0183
      </li>
      <li>
        <svg width="15" height="15" viewBox="0 0 16 16"><circle cx="8" cy="8" r="7" fill="none" stroke="var(--green)" stroke-width="1.5"/><rect x="4.5" y="7" width="7" height="4" fill="var(--green)"/><rect x="6" y="4.5" width="4" height="2.5" fill="none" stroke="var(--green)" stroke-width="1"/></svg>
        (402) 555-0129
      </li>
    </ul>

    <ul class="contact-list contact-list--online">
      <li>
        <svg width="15" height="15" viewBox="0 0 16 16"><circle cx="8" cy="8" r="7" fill="none" stroke="var(--green)" stroke-width="1.5"/><rect x="4.5" y="5.5" width="7" height="5" fill="none" stroke="var(--green)" stroke-width="1.1"/><path d="M4.5 5.5 L8 8.5 11.5 5.5" fill="none" stroke="var(--green)" stroke-width="1.1"/></svg>
        tobias@meridaleplan.example
      </li>
      <li>
        <svg width="15" height="15" viewBox="0 0 16 16"><circle cx="8" cy="8" r="7" fill="none" stroke="var(--green)" stroke-width="1.5"/><circle cx="8" cy="8" r="3.6" fill="none" stroke="var(--green)" stroke-width="1"/><path d="M4.4 8 H11.6 M8 4.4 V11.6" stroke="var(--green)" stroke-width="1"/></svg>
        www.meridaleplan.example
      </li>
    </ul>

    <address class="address">
      5287 E. Larkin Road<br>
      Suite 230<br>
      Omaha, NE 68190
    </address>

    <p class="disclosure">Advisory services offered through Stonebrook Assets, LLC.</p>
  </section>

</main>
</body>
</html>
```